CFO services graphic design

I own a business consulting firm called Thornfield Advisory and we need a graphic for CFO services in our colours and branding. The attached file "CFO services to be put into Thornfield advisory theme", shows the content for the design. The two other files show the theme and colours for the new design.

```html
<!DOCTYPE html>
<html lang="en">
<head>
<meta charset="utf-8">
<title>Thornfield Advisory – CFO Services</title>
<link rel="stylesheet" href="https://fonts.googleapis.com/css2?family=Roboto+Condensed:wght@400;600&family=Roboto:wght@700&display=swap">
<style>
  :root {
    --bg: #ffffff;
    --cost: #4dd6fd;
    --communication: #4dbbfb;
    --compliance: #3698fc;
    --risk: #3179e3;
    --budgeting: #1b5cce;
    --performance: #163fa0;
    --investment: #03287c;
    --capital: #011459;
    --accent: #ff7f0e;
    --ring-light: #4dd6fd;
    --label: #ffffff;
  }
  html, body {
    margin: 0;
    padding: 0;
    width: 1200px;
    height: 1000px;
    overflow: hidden;
    background: var(--bg);
  }
  .cfo-diagram {
    display: block;
    width: 1200px;
    height: 1000px;
  }
  .petal {
    stroke: var(--bg);
    stroke-width: 21;
  }
  .petal--cost { fill: var(--cost); }
  .petal--communication { fill: var(--communication); }
  .petal--compliance { fill: var(--compliance); }
  .petal--risk { fill: var(--risk); }
  .petal--budgeting { fill: var(--budgeting); }
  .petal--performance { fill: var(--performance); }
  .petal--investment { fill: var(--investment); }
  .petal--capital { fill: var(--capital); }
  .hub { fill: var(--bg); }
  .hub-ring { fill: none; stroke-width: 16; }
  .hub-ring--accent { stroke: var(--accent); }
  .hub-ring--light { stroke: var(--ring-light); }
  .petal-title {
    font-family: "Roboto Condensed", sans-serif;
    font-weight: 600;
    font-size: 35px;
    letter-spacing: -0.6px;
    fill: var(--label);
    text-anchor: middle;
  }
  .petal-detail {
    font-family: "Roboto Condensed", sans-serif;
    font-weight: 400;
    font-size: 31px;
    letter-spacing: -0.9px;
    fill: var(--label);
    text-anchor: middle;
  }
  .hub-title {
    font-family: "Roboto", sans-serif;
    font-weight: 700;
    font-size: 76px;
    letter-spacing: -2px;
    fill: var(--accent);
    text-anchor: middle;
  }
</style>
</head>
<body>
<svg class="cfo-diagram" viewBox="0 0 2100 1750" role="img" aria-label="Chief Financial Officer services diagram">
  <defs>
    <clipPath id="communication-overlap">
      <rect x="870" y="150" width="260" height="450"/>
    </clipPath>
  </defs>

  <g class="petals">
    <circle class="petal petal--communication" cx="758" cy="492" r="233"/>
    <circle class="petal petal--compliance" cx="573" cy="810" r="233"/>
    <circle class="petal petal--risk" cx="667" cy="1167" r="233"/>
    <circle class="petal petal--budgeting" cx="985" cy="1352" r="233"/>
    <circle class="petal petal--performance" cx="1342" cy="1258" r="233"/>
    <circle class="petal petal--investment" cx="1527" cy="940" r="233"/>
    <circle class="petal petal--capital" cx="1432" cy="583" r="233"/>
    <circle class="petal petal--cost" cx="1115" cy="398" r="233"/>
    <circle class="petal petal--communication" cx="758" cy="492" r="233" clip-path="url(#communication-overlap)"/>
  </g>

  <circle class="hub" cx="1050" cy="875" r="325"/>
  <path class="hub-ring hub-ring--light" d="M1050 615 A260 260 0 0 1 1050 1135"/>
  <path class="hub-ring hub-ring--accent" d="M1050 1135 A260 260 0 0 1 1050 615"/>

  <g class="hub-label">
    <text class="hub-title" x="1050" y="812">CHIEF</text>
    <text class="hub-title" x="1050" y="898">FINANCIAL</text>
    <text class="hub-title" x="1050" y="984">OFFICER</text>
  </g>

  <g class="petal-labels">
    <text class="petal-title" x="1156" y="382">COST ACCOUNTING &amp;</text>
    <text class="petal-title" x="1156" y="433">COST MANAGEMENT</text>

    <text class="petal-title" x="760" y="393">COMMUNICATION:</text>
    <text class="petal-detail" x="760" y="443">BOARD OF DIRECTORS,</text>
    <text class="petal-detail" x="760" y="480">CREDITORS, OWNERS,</text>
    <text class="petal-detail" x="760" y="517">INVESTORS, CREDIT</text>
    <text class="petal-detail" x="760" y="554">RATING AGENCIES</text>

    <text class="petal-title" x="566" y="753">COMPLIANCE:</text>
    <text class="petal-detail" x="566" y="804">TAX, LEGAL AND</text>
    <text class="petal-detail" x="566" y="841">REGULATORY</text>

    <text class="petal-title" x="636" y="1172">RISK MANAGEMENT</text>

    <text class="petal-title" x="952" y="1349">BUDGETING &amp;</text>
    <text class="petal-title" x="952" y="1400">STRATEGIC PLANNING</text>

    <text class="petal-title" x="1337" y="1266">PERFORMANCE</text>
    <text class="petal-title" x="1337" y="1317">EVALUATION</text>

    <text class="petal-title" x="1546" y="910">LONG-TERM &amp;</text>
    <text class="petal-title" x="1546" y="961">SHORT-TERM</text>
    <text class="petal-title" x="1546" y="1012">INVESTMENT DECISIONS</text>

    <text class="petal-title" x="1462" y="525">CAPITAL</text>
    <text class="petal-title" x="1462" y="576">STRUCTURE &amp;</text>
    <text class="petal-title" x="1462" y="627">THE COST OF CAPITAL</text>
  </g>
</svg>
</body>
</html>
```